Business card for denture clinic Veltrimora

We need a new business card with our new logo. We are a denture clinic in New Zealand with our target market being 45+ years old. We would need a space on the back to write our patients next appointment on. We would space for only one appointment rather than a list. We will attach a photo showing an example of this. But of course, we would like to see your twist on this. We want it to be bold and easy to read and a good mixture of professional but modern. We have attached our logo to be used on the card.

Target Market(s)

People aged 45+ needing dentures

Industry/Entity Type

Dental

Contact Information for Business Card

We want our logo on the front and the space to write an appointment on the back. I've attached an example our our old business card showing this. We need to have the technicians details on the front.

Font styles to use
Sans Serif

Colors
0255a3
919191
fbfbfb

Requirements
Must have
• The following details:
• Liam Dorsett BDT, PGDipCDentTech Calverin
• Dental Prosthetist
• Phone numbers: 0800 47 3125
• 09 572 1394
• Email: liam@veltrimora.co.nz
• www.veltrimora.co.nz
• Address: 14 Marlow Crest Road
• Halbrook West
• Auckland 0793
Nice to have
• We would like our business cards to have more than just two colours as we want them to be more vibrant. We have uploaded an example of a business card we liked that showed this.

```html
<!DOCTYPE html>
<html lang="en">
<head>
<meta charset="utf-8">
<title>Veltrimora – Business Card</title>
<link href="https://fonts.googleapis.com/css2?family=Exo+2:wght@500;700;800&family=Open+Sans:wght@400;600&display=swap" rel="stylesheet">
<style>
  :root {
    --brand-blue: #0255a3;
    --bar-blue: #1f6fbd;
    --text-grey: #6f6f6f;
    --soft-grey: #919191;
    --card-white: #fbfbfb;
    --stage: #e6e8eb;
  }
  * { box-sizing: border-box; margin: 0; padding: 0; }
  html, body { width: 1200px; height: 1000px; overflow: hidden; }
  body {
    background: var(--stage);
    font-family: "Open Sans", sans-serif;
    position: relative;
  }
  .card {
    position: absolute;
    left: 250px;
    width: 700px;
    height: 400px;
    background: var(--card-white);
    border-radius: 24px;
    box-shadow: 0 10px 30px rgba(0,0,0,0.12);
    overflow: hidden;
  }
  .card--front { top: 70px; }
  .card--back { top: 530px; }

  /* brand */
  .brand {
    position: absolute;
    display: flex;
    align-items: center;
    gap: 10px;
  }
  .brand__square {
    width: 34px; height: 34px;
    background: var(--brand-blue);
    border-radius: 4px;
  }
  .brand__name {
    font-family: "Exo 2", sans-serif;
    font-weight: 800;
    font-size: 30px;
    letter-spacing: 0.5px;
    color: var(--brand-blue);
    text-transform: uppercase;
    line-height: 34px;
  }
  .card--front .brand { right: 44px; top: 152px; }
  .card--back .brand { left: 200px; top: 70px; }

  /* front */
  .holder { position: absolute; left: 44px; top: 60px; }
  .holder__name {
    font-family: "Exo 2", sans-serif;
    font-weight: 700;
    font-size: 30px;
    line-height: 36px;
    color: var(--brand-blue);
    text-transform: uppercase;
    letter-spacing: 0.5px;
  }
  .holder__role {
    font-size: 17px;
    line-height: 23px;
    color: var(--text-grey);
    margin-top: 2px;
  }
  .holder__credential {
    font-size: 13px;
    line-height: 18px;
    color: var(--soft-grey);
    margin-top: 2px;
  }
  .divider {
    position: absolute;
    left: 205px; top: 116px;
    width: 340px; height: 2px;
    background: var(--brand-blue);
  }
  .contacts {
    position: absolute;
    left: 44px; top: 160px;
    list-style: none;
    font-size: 14px;
    color: var(--text-grey);
    line-height: 24px;
  }
  .contacts li { display: flex; align-items: center; gap: 10px; }
  .contacts svg { width: 13px; height: 13px; fill: none; stroke: var(--brand-blue); stroke-width: 2; }
  .contacts .web span { color: var(--brand-blue); }
  .address {
    position: absolute;
    right: 160px; top: 272px;
    text-align: right;
    font-style: normal;
    font-family: "Exo 2", sans-serif;
    font-weight: 500;
    font-size: 16px;
    line-height: 22px;
    color: var(--text-grey);
  }

  /* back */
  .slot {
    position: absolute;
    height: 34px;
    width: 260px;
    background: var(--bar-blue);
    border-radius: 6px;
    display: flex;
    align-items: center;
    padding: 0 14px;
    gap: 8px;
    color: #fff;
    font-size: 17px;
  }
  .slot__fill {
    flex: 1;
    border-bottom: 2px dotted rgba(255,255,255,0.85);
    height: 16px;
  }
  .slot--date { left: 40px; top: 160px; }
  .slot--time { right: 40px; top: 290px; }
  .appointment-label {
    position: absolute;
    left: 0; right: 0; top: 225px;
    text-align: center;
    font-size: 22px;
    color: var(--bar-blue);
    letter-spacing: 0.3px;
  }
</style>
</head>
<body>

<section class="card card--front" aria-label="Business card front">
  <div class="holder">
    <h1 class="holder__name">Liam Dorsett BDT</h1>
    <p class="holder__role">Dental Prosthetist</p>
    <p class="holder__credential">BDT, PGDipCDentTech Calverin</p>
  </div>
  <div class="divider"></div>
  <ul class="contacts">
    <li>
      <svg viewBox="0 0 14 14"><path d="M3 1 L5 1 L6 4 L4.5 5.5 Q6 8.5 8.5 9.5 L10 8 L13 9 L13 11 Q12 13 10 13 Q2 11 1 3 Q1 1 3 1Z"/></svg>
      <span>0800 47 3125</span>
    </li>
    <li>
      <svg viewBox="0 0 14 14"><rect x="3.5" y="1" width="7" height="12" rx="1.5"/></svg>
      <span>09 572 1394</span>
    </li>
    <li>
      <svg viewBox="0 0 14 14"><rect x="1" y="3" width="12" height="8"/><path d="M1 3 L7 8 L13 3"/></svg>
      <span>liam@veltrimora.co.nz</span>
    </li>
    <li class="web">
      <svg viewBox="0 0 14 14"><circle cx="8" cy="6" r="4"/><path d="M5 9 L1 13"/></svg>
      <span>www.veltrimora.co.nz</span>
    </li>
  </ul>
  <div class="brand">
    <span class="brand__square"></span>
    <span class="brand__name">Veltrimora</span>
  </div>
  <address class="address">
    14 Marlow Crest Road,<br>
    Halbrook West<br>
    Auckland 0793
  </address>
</section>

<section class="card card--back" aria-label="Business card back">
  <div class="brand">
    <span class="brand__square"></span>
    <span class="brand__name">Veltrimora</span>
  </div>
  <div class="slot slot--date"><span>date:</span><span class="slot__fill"></span></div>
  <p class="appointment-label">your next appointment</p>
  <div class="slot slot--time"><span>time:</span><span class="slot__fill"></span></div>
</section>

</body>
</html>
```